NEW Modern Sleek Business Card for VR Language Startup

Our startup is using VR to lead the next wave of world language education. We need a two-sided business card that introduces the larger organization (Brightloom Language Inc) and our contact info on one side and shows the product, Glimwoorld, on the other side.

Side 1 (contact info)= Brightloom Logo and Contact info (name, title, phone, email)

Side 2 (product)= Glimworld logo, text, and website
Text= Culturally Immersive Language Learning Games
Website= www.glimworld-play.com

Target Market(s)

Education, Technology

Contact Information for Business Card

Contact info will be updated upon approval of the design. For now, put this as a placeholder.

Perry Dunmore
Founder & CEO
pdunmore@quillpost-mail.net
(555)-014-2286

Font styles to use
Other font styles liked:
• Gibson and Century Gothic are the brand fonts

Requirements
Nice to have
• I would love to see cohesion between the design and colors of the two logos. I have attached a few business card designs that I like, so you can get a feel for my preferred style.

```html
<!DOCTYPE html>
<html lang="en">
<head>
<meta charset="utf-8">
<title>Brightloom Language – Business Card</title>
<link href="https://fonts.googleapis.com/css2?family=Lato:wght@400;700&display=swap" rel="stylesheet">
<style>
  :root {
    --backdrop: #404040;
    --card-white: #ffffff;
    --ink: #1c1c1c;
    --ink-soft: #222222;
    --accent-orange: #f26b3a;
    --accent-violet: #7a5cf0;
    --product-cyan: #22d9ea;
    --product-blue: #3f9cf0;
    --product-violet: #5d66f2;
    --on-product: #ffffff;
  }
  * { box-sizing: border-box; margin: 0; padding: 0; }
  html, body {
    width: 1200px; height: 900px; overflow: hidden;
    background: var(--backdrop);
    font-family: "Lato", Arial, sans-serif;
  }
  .canvas { position: relative; width: 1200px; height: 900px; }

  .card {
    position: absolute; top: 200px;
    width: 310px; height: 502px;
  }

  /* Contact side */
  .card--contact {
    left: 253px;
    background: var(--card-white);
    border-radius: 62px 0 62px 0;
  }
  .brand-lockup {
    position: absolute; left: 0; right: 0; top: 96px;
    display: flex; flex-direction: column; align-items: center; gap: 22px;
  }
  .brand-dot {
    width: 86px; height: 86px; border-radius: 50%;
    background: var(--accent-orange);
  }
  .brand-name {
    font-weight: 700; font-size: 40px; letter-spacing: 1px;
    color: var(--ink);
  }
  .contact {
    position: absolute; left: 33px; top: 350px;
    color: var(--ink-soft);
  }
  .contact__name {
    font-weight: 700; font-size: 20px; line-height: 22px;
    background: linear-gradient(90deg, var(--accent-orange), var(--accent-violet));
    -webkit-background-clip: text; background-clip: text; color: transparent;
    text-transform: uppercase;
  }
  .contact__title { font-size: 14.5px; line-height: 18px; }
  .contact__lines { margin-top: 28px; list-style: none; font-size: 14.5px; line-height: 19px; }
  .contact__lines li { display: flex; align-items: center; gap: 4px; }
  .contact__icon { width: 13px; height: 13px; flex: none; }

  /* Product side */
  .card--product {
    left: 627px;
    border-radius: 0 62px 0 62px;
    background: linear-gradient(150deg, var(--product-cyan) 0%, var(--product-blue) 50%, var(--product-violet) 100%);
    color: var(--on-product);
    text-align: center;
  }
  .product-name {
    position: absolute; left: 0; right: 0; top: 248px;
    font-weight: 700; font-size: 40px;
  }
  .product-tagline {
    position: absolute; left: 0; right: 0; top: 351px;
    font-size: 15px; line-height: 19px; text-transform: uppercase;
  }
  .product-site {
    position: absolute; left: 0; right: 0; top: 439px;
    font-weight: 700; font-size: 15.5px;
  }
</style>
</head>
<body>
<main class="canvas">
  <section class="card card--contact" aria-label="Contact side">
    <div class="brand-lockup">
      <span class="brand-dot" aria-hidden="true"></span>
      <span class="brand-name">Brightloom</span>
    </div>
    <div class="contact">
      <p class="contact__name">Perry Dunmore</p>
      <p class="contact__title">Founder &amp; CEO</p>
      <ul class="contact__lines">
        <li>
          <svg class="contact__icon" viewBox="0 0 16 16" aria-hidden="true">
            <path d="M3 5 Q8 1 13 5 L11 7 L9.5 6 L6.5 6 L5 7 Z M4.5 9 H11.5 L12.5 14 H3.5 Z" fill="#f26b3a"/>
          </svg>
          <span>(555)-014-2286</span>
        </li>
        <li>
          <svg class="contact__icon" viewBox="0 0 16 16" aria-hidden="true">
            <rect x="1" y="3.5" width="14" height="9.5" fill="#7a5cf0"/>
            <path d="M1 3.5 L8 9 L15 3.5" stroke="#fff" stroke-width="1.3" fill="none"/>
          </svg>
          <span>pdunmore@quillpost-mail.net</span>
        </li>
      </ul>
    </div>
  </section>

  <section class="card card--product" aria-label="Product side">
    <p class="product-name">Glimworld</p>
    <p class="product-tagline">Culturally immersive<br>language learning games</p>
    <p class="product-site">www.glimworld-play.com</p>
  </section>
</main>
</body>
</html>
```